Mortgage Protection Insurance Flyer

The target audience are new home owners so the design needs to be clean and simple.

This a primarily for Final Expense Insurance, but need an area where it says "We Also Specialize In:"
- Medicare Supplement Insurance (MediGap)
- Annuities
- Final Expense

All flyer versions need to be editable. Colors to be used are red, white or black. Refer to my website for colors and photos (corvantshield.com). Will attach my logo and a flyer that I found online that is the format that I am looking for (for 8.5 in. x 11 in version). Need flyer in standard letter size 8.5 in. x11 in. but also in 8.5 in. x 5.5 in and 5.0 in. x 8.0 in. All sizes to be portrait oriented. If picked as winning design, need all flyer versions in full color, also in grey scale and files in all industry file types.

Content can be taken from my website..... corvantshield.com

Do NOT submit if you are not willing to provide all versions as described above for the original project price.

Must use royalty-free stock photos please.

Target Market(s)

New homeowners looking for insurance to protect there mortgage payments

Industry/Entity Type

Life Insurance

Colors
f69fa3

Requirements
Must have
• Colors to be used are red, white or black.
• Need flyer in standard letter size 8.5 in. x11 in. but also in 3.5 in. x 8.5 in (Full Bleed 3.75 in by 8.75 in.) and 4.0 in. x 6.0 in. (Full Bleed 4.12 in x 6.12 in) Each design tailored to the size dimensions (So no squeezing 8.5 x 11 design into a 4.0 x 6.0 space.) All sizes to be portrait oriented. If picked as winning design, need all flyer versions in full color, also in grey scale and files in all file types.
• Do not need physical address on flyer, do need email address on flyer though - tkelwer@corvantshield.com
• So phone number should be prominent, email address and website address should also be contact area.
• If you can not agree to terms above, do not submit any designs.
• Need facebook & twitter logos somewhere in contact info area.
Nice to have
• See sample flyers I have attached.
• White background with red used as primary graphic color and black used as secondary graphic if needed.
• font to be used should similar to one used in logo.

```html
<!DOCTYPE html>
<html lang="en">
<head>
<meta charset="utf-8">
<title>Corvant Shield Flyer Set</title>
<link href="https://fonts.googleapis.com/css2?family=Oswald:wght@600;700&family=Lato:wght@400;700;900&display=swap" rel="stylesheet">
<style>
:root{
  --red:#e8000b;
  --red-dark:#a8141c;
  --black:#1c1c1c;
  --grey:#cfcfcf;
  --text:#2a2a2a;
  --white:#fff;
  --pink-a:#f6b0b1;
  --pink-b:#f29696;
  --photo-a:#eef0f2;
  --photo-b:#d9d6d0;
}
*{box-sizing:border-box;margin:0;padding:0}
html,body{width:1200px;height:1200px;overflow:hidden}
body{font-family:"Lato",sans-serif;color:var(--text);position:relative;
  background:linear-gradient(90deg,var(--pink-a) 0 643px,var(--pink-b) 643px 100%)}
.piece{position:absolute;background:var(--white);overflow:hidden}
.piece svg.shapes{position:absolute;left:0;top:0}
.abs{position:absolute}
.photo{position:absolute;left:0;top:0;background:linear-gradient(110deg,var(--photo-a) 35%,var(--photo-b) 100%)}
.brand{position:absolute;font-family:"Lato",sans-serif;font-weight:900;color:var(--black);white-space:nowrap}
.headline{position:absolute;font-family:"Oswald",sans-serif;font-weight:700;color:var(--black);text-transform:uppercase;white-space:nowrap}
.headline span{display:block}
.headline .red{color:var(--red)}
.headline .sub{font-weight:600}
.section-title{position:absolute;font-weight:900;color:var(--red);line-height:1.1}
.body-copy{position:absolute;line-height:1.3}
.body-copy p+p{margin-top:.9em}
.benefits{position:absolute;border-radius:10px;background:linear-gradient(180deg,#ff0a0a 0%,var(--red) 45%,var(--red-dark) 100%);color:var(--white);font-weight:700}
.benefits .tab{position:absolute;left:-6px;background:#333;color:var(--white);border-radius:0 8px 8px 0;font-weight:700}
.benefits ul{list-style:none}
.tick{display:inline-block;position:relative;border-radius:50%;border:1px solid currentColor;flex:none}
.tick::after{content:"";position:absolute;left:30%;top:18%;width:28%;height:45%;border:solid currentColor;border-width:0 1px 1px 0;transform:rotate(45deg)}
.benefits li{display:flex;gap:4px}
.rate-table{position:absolute}
.rate-table .row{display:flex;justify-content:space-between;align-items:center}
.rate-table .label{background:var(--grey);color:var(--black);font-weight:700}
.rate-table .value{background:var(--red);color:var(--white);font-weight:900;text-align:center}
.spec-list{position:absolute;list-style:none}
.spec-list li{position:absolute;display:flex;align-items:center;gap:4px;white-space:nowrap}
.spec-list .tick{color:var(--red)}
.contact{position:absolute;color:var(--white)}
.contact .call{font-weight:700}
.contact .phone{font-weight:700;letter-spacing:.3px}
.contact-line{position:absolute;display:flex;align-items:center;gap:6px;color:var(--white);font-weight:700;white-space:nowrap}
.ring{border:1px solid var(--white);border-radius:50%;display:flex;align-items:center;justify-content:center;flex:none}
.social{position:absolute;display:flex;gap:2px}
.social span{background:var(--white);border-radius:1px}
.blank-back{position:absolute;background:var(--white)}
</style>
</head>
<body>

<!-- Postcard front -->
<section class="piece postcard-front" style="left:73px;top:207px;width:500px;height:333px">
  <div class="photo" role="img" aria-label="Photo of a smiling senior couple embracing in a bright living room" style="width:500px;height:215px"></div>
  <svg class="shapes" width="500" height="333" viewBox="0 0 500 333" aria-hidden="true">
    <path d="M0 0H215C175 45 95 78 0 80Z" fill="#fff"/>
    <path d="M215 0C175 45 95 78 0 80" fill="none" stroke="#1c1c1c" stroke-width="4"/>
    <path d="M222 0C182 48 100 84 0 87" fill="none" stroke="#e8000b" stroke-width="1.5"/>
    <path d="M0 196C120 188 260 182 340 184C420 186 475 205 500 226" fill="none" stroke="#1c1c1c" stroke-width="6"/>
    <path d="M0 203C120 195 260 189 340 191C420 193 475 212 500 233" fill="none" stroke="#e8000b" stroke-width="2"/>
    <path d="M0 206C120 198 260 192 340 194C420 196 475 215 500 236V333H0Z" fill="#fff"/>
    <rect x="0" y="324" width="500" height="2" fill="#1c1c1c"/>
    <rect x="0" y="328" width="500" height="3" fill="#e8000b"/>
  </svg>
  <div class="brand" style="left:31px;top:31px;font-size:12.5px">CORVANT SHIELD</div>
  <h1 class="headline" style="left:28px;top:88px;font-size:31px;line-height:32px">
    <span>Our</span>
    <span class="red">Plans Are</span>
    <span class="sub" style="font-size:19px;line-height:24px">Based on Yours</span>
  </h1>
  <h2 class="section-title" style="left:28px;top:219px;font-size:13px">Final Expense Insurance</h2>
  <p class="body-copy" style="left:28px;top:241px;width:232px;font-size:6.4px">Final Expense Insurance is a type of permanent whole life insurance where the death benefit is used to cover (but not limited to) medical costs, funeral costs and other end-of-life expenses. It is a budget friendly option with a death benefit of up to $40k.</p>
  <div class="rate-table" style="left:28px;top:279px;width:172px;font-size:6.8px">
    <div class="row" style="height:12px"><span class="label" style="width:104px;padding:2px 4px">Monthly premiums as low as</span><span class="value" style="width:45px;padding:2px 0">$11*</span></div>
    <div class="row" style="height:12px;margin-top:4px"><span class="label" style="width:104px;padding:2px 4px">Death Benefits as high as</span><span class="value" style="width:45px;padding:2px 0">$40,000</span></div>
  </div>
  <div class="benefits" style="left:275px;top:138px;width:205px;height:180px;font-size:6.3px">
    <div class="tab" style="top:14px;padding:2px 12px 2px 14px;font-size:6.5px">Benefits:</div>
    <ul style="padding:31px 10px 0 9px">
      <li style="margin-bottom:10px"><span class="tick" style="width:7px;height:7px"></span>All plans we offer are state regulated</li>
      <li style="margin-bottom:10px"><span class="tick" style="width:7px;height:7px"></span>Relatively low monthly premiums</li>
      <li style="margin-bottom:10px"><span class="tick" style="width:7px;height:7px"></span>Premiums can never increase</li>
      <li style="margin-bottom:10px"><span class="tick" style="width:7px;height:7px"></span>Your policy can never be cancelled as long as you pay your premium</li>
      <li style="margin-bottom:10px"><span class="tick" style="width:7px;height:7px"></span>No medical exams</li>
      <li style="margin-bottom:10px"><span class="tick" style="width:7px;height:7px"></span>Guaranteed Death Benefit</li>
      <li><span class="tick" style="width:7px;height:7px"></span>Many policies we offer are Guaranteed Acceptance, "Day 1" coverage, have a child/grandchild rider and/or have an accelerated death benefit rider</li>
    </ul>
  </div>
</section>

<!-- Postcard back -->
<section class="piece postcard-back" style="left:73px;top:646px;width:500px;height:333px">
  <div class="blank-back" style="left:283px;top:0;width:217px;height:333px;box-shadow:-2px 0 4px rgba(0,0,0,.08)"></div>
  <svg class="shapes" width="283" height="333" viewBox="0 0 283 333" aria-hidden="true">
    <defs><linearGradient id="redBandA" x1="0" y1="0" x2="0" y2="1"><stop offset="0" stop-color="#e8000b"/><stop offset="1" stop-color="#8e1218"/></linearGradient></defs>
    <path d="M0 240C70 226 180 236 283 250" fill="none" stroke="#1c1c1c" stroke-width="4"/>
    <path d="M0 246C70 232 180 242 283 256V333H0Z" fill="url(#redBandA)"/>
    <rect x="155" y="33" width="1.5" height="30" fill="#e8000b"/>
  </svg>
  <div class="brand" style="left:29px;top:41px;font-size:12.5px">CORVANT SHIELD</div>
  <p class="abs" style="left:168px;top:38px;font-size:8.5px;line-height:1.3">PO Box 412<br>Larchmere, ID 83000</p>
  <div class="body-copy" style="left:23px;top:84px;width:245px;font-size:6.4px">
    <p>We have been helping clients in Northern Idaho/Eastern Washington prepare for the unknown.</p>
    <p>We have access to the industry's top insurance carriers so you can get the right coverage, that fits your budget.</p>
    <p>Find out how we can give you the peace of mind of knowing your family will not have a financial burden if something were to happen to you.</p>
  </div>
  <h3 class="section-title" style="left:24px;top:159px;font-size:7.5px">We Also Specialize In:</h3>
  <ul class="spec-list" style="left:24px;top:175px;font-size:6.4px">
    <li style="left:0;top:0"><span class="tick" style="width:8px;height:8px"></span>Medicare Supplement Insurance (Medigap)</li>
    <li style="left:168px;top:0"><span class="tick" style="width:8px;height:8px"></span>Annuities</li>
    <li style="left:0;top:18px"><span class="tick" style="width:8px;height:8px"></span>Mortgage Protection Insurance</li>
  </ul>
  <p class="abs" style="left:105px;top:208px;width:160px;font-size:4.8px;line-height:1.3">*Based on an insured that is a 65 year old, non-smoking female that has no medical conditions with a death benefit of $2k</p>
  <div class="contact" style="left:25px;top:256px">
    <div style="font-size:10.5px;line-height:1.2;padding-bottom:3px;border-bottom:1px solid rgba(255,255,255,.7);width:86px">GUARANTEED<br>APPROVAL!</div>
    <div class="call" style="font-size:10px;margin-top:7px">Call us now:</div>
    <div class="phone" style="font-size:15px">(208)555.0147</div>
  </div>
  <div class="contact-line" style="left:140px;top:283px;font-size:6px"><span class="ring" style="width:15px;height:15px"><svg width="8" height="6" viewBox="0 0 8 6"><rect x=".5" y=".5" width="7" height="5" fill="none" stroke="#fff" stroke-width=".8"/><path d="M.5 .5L4 3.5 7.5 .5" fill="none" stroke="#fff" stroke-width=".8"/></svg></span>tkelwer@corvantshield.com</div>
  <div class="contact-line" style="left:140px;top:303px;font-size:6px"><span class="ring" style="width:15px;height:15px"><svg width="9" height="9" viewBox="0 0 10 10"><circle cx="5" cy="5" r="4.2" fill="none" stroke="#fff" stroke-width=".8"/><ellipse cx="5" cy="5" rx="1.9" ry="4.2" fill="none" stroke="#fff" stroke-width=".8"/><path d="M.8 5H9.2" stroke="#fff" stroke-width=".8"/></svg></span>corvantshield.com</div>
  <div class="social" style="left:250px;top:310px"><span style="width:7px;height:7px"></span><span style="width:7px;height:7px"></span></div>
</section>

<!-- Letter flyer -->
<section class="piece flyer" style="left:728px;top:137px;width:377px;height:879px">
  <div class="photo" role="img" aria-label="Photo of a smiling senior couple embracing on a sofa" style="width:377px;height:330px"></div>
  <svg class="shapes" width="377" height="879" viewBox="0 0 377 879" aria-hidden="true">
    <defs><linearGradient id="redBandB" x1="0" y1="0" x2="0" y2="1"><stop offset="0" stop-color="#e8000b"/><stop offset="1" stop-color="#8e1218"/></linearGradient></defs>
    <path d="M0 0H255C205 70 110 104 0 105Z" fill="#fff"/>
    <path d="M255 0C205 70 110 104 0 105" fill="none" stroke="#1c1c1c" stroke-width="5"/>
    <path d="M264 0C212 76 114 112 0 113" fill="none" stroke="#e8000b" stroke-width="2"/>
    <path d="M0 296C90 320 250 296 377 280" fill="none" stroke="#1c1c1c" stroke-width="7"/>
    <path d="M0 304C90 328 250 304 377 288" fill="none" stroke="#e8000b" stroke-width="2.5"/>
    <path d="M0 308C90 332 250 308 377 292V879H0Z" fill="#fff"/>
    <path d="M0 777C110 750 260 790 377 743" fill="none" stroke="#1c1c1c" stroke-width="6"/>
    <path d="M0 784C110 757 260 797 377 750V879H0Z" fill="url(#redBandB)"/>
  </svg>
  <div class="brand" style="left:29px;top:38px;font-size:17px">CORVANT SHIELD</div>
  <h1 class="headline" style="left:28px;top:162px;font-size:38px;line-height:40px">
    <span>Our</span>
    <span class="red">Plans Are</span>
    <span class="sub" style="font-size:23px;line-height:30px">Based on Yours</span>
  </h1>
  <h2 class="section-title" style="left:30px;top:345px;font-size:12px">Mortgage Protection<br>Insurance</h2>
  <div class="body-copy" style="left:31px;top:380px;width:130px;font-size:8.2px;text-align:justify">
    <p>Mortgage Protection Insurance (MPI) is a type of decreasing term life insurance policy designed to pay off your mortgage if you were to pass away — and many policies also cover mortgage payments (usually for a limited period of time) if you become disabled.</p>
    <p>Unforeseen events and a lack of the right kind of insurance can spell trouble quickly. Contact us today, to set up a free assessment time. We will analyze your insurance needs and get you and your family the right coverage quickly at a budget friendly price.</p>
  </div>
  <div class="benefits" style="left:186px;top:340px;width:154px;height:206px;font-size:6.4px">
    <div class="tab" style="top:16px;padding:2px 14px 2px 16px;font-size:8px">Benefits:</div>
    <ul style="padding:39px 10px 0 12px;line-height:1.3">
      <li style="margin-bottom:10px"><span class="tick" style="width:8px;height:8px"></span>Guaranteed approval. Even if you're in poor health or work in a dangerous profession, there is guaranteed approval with no medical exams or lab tests.</li>
      <li style="margin-bottom:10px"><span class="tick" style="width:8px;height:8px"></span>No guesswork. The check goes straight to the lender for the exact mortgage balance, so there'll always be enough and your family won't have to handle the money.</li>
      <li><span class="tick" style="width:8px;height:8px"></span>Disability protection. Many MPI policies make mortgage payments (usually for a limited time) if you become disabled or lose your job.</li>
    </ul>
  </div>
  <div class="body-copy" style="left:31px;top:592px;width:310px;font-size:8.6px">
    <p>We have been helping clients in Northern Idaho/Eastern Washington prepare for the unknown.</p>
    <p style="margin-top:11px">We have access to the industry's top insurance carriers so you can get the right coverage, that fits your budget.</p>
    <p style="margin-top:14px">Find out how we can give you the peace of mind of knowing your family will not have a financial burden if something were to happen to you.</p>
  </div>
  <h3 class="section-title" style="left:31px;top:703px;font-size:12px">We Also Specialize In:</h3>
  <ul class="spec-list" style="left:31px;top:725px;font-size:8.6px">
    <li style="left:0;top:0"><span class="tick" style="width:10px;height:10px"></span>Medicare Supplement Insurance (Medigap)</li>
    <li style="left:205px;top:1px"><span class="tick" style="width:10px;height:10px;margin-right:6px"></span>Annuities</li>
    <li style="left:0;top:15px"><span class="tick" style="width:10px;height:10px"></span>Final Expense Insurance</li>
  </ul>
  <div class="contact" style="left:26px;top:802px">
    <div class="call" style="font-size:12px">Call us now:</div>
    <div class="phone" style="font-size:19px;margin-top:2px">(208)555.0147</div>
  </div>
  <div class="contact-line" style="left:175px;top:801px;font-size:7.3px"><span class="ring" style="width:20px;height:20px"><svg width="10" height="8" viewBox="0 0 8 6"><rect x=".5" y=".5" width="7" height="5" fill="none" stroke="#fff" stroke-width=".7"/><path d="M.5 .5L4 3.5 7.5 .5" fill="none" stroke="#fff" stroke-width=".7"/></svg></span>tkelwer@corvantshield.com</div>
  <div class="contact-line" style="left:175px;top:825px;font-size:7.3px"><span class="ring" style="width:20px;height:20px"><svg width="12" height="12" viewBox="0 0 10 10"><circle cx="5" cy="5" r="4.2" fill="none" stroke="#fff" stroke-width=".7"/><ellipse cx="5" cy="5" rx="1.9" ry="4.2" fill="none" stroke="#fff" stroke-width=".7"/><path d="M.8 5H9.2" stroke="#fff" stroke-width=".7"/></svg></span>corvantshield.com</div>
  <div class="social" style="left:297px;top:851px"><span style="width:9px;height:9px"></span><span style="width:9px;height:9px"></span></div>
</section>

</body>
</html>
```